Dovecote Realty

Business cards for 4 people

They need to say for all
87 Tarrow Quay, Boston MA 02114

Each person will have their own personal information
We would like gold embossing for the name of the company
Marla is the blonde sitting in the chair smiling her information should be on the back of the card with her name and information
Should say for slogan classic pattern, elevated experience
grace@dovecoteprops.com
(413) 555-0182

Odette is the brunette with wavy hair in the tan suit odette@dovecoteprops.com
(617) 555-0137

faith@dovecoteprops.com
(413) 555-0164
standing next to the chair

hope@dovecoteprops.com
(413) 555-0199
close up headshot

```html
<!DOCTYPE html>
<html lang="en">
<head>
<meta charset="utf-8">
<title>Dovecote Realty – Business Cards</title>
<link rel="stylesheet" href="https://fonts.googleapis.com/css2?family=Open+Sans:wght@400;600;700&display=swap">
<style>
  :root {
    --stage: #232323;
    --navy: #22305a;
    --gold: #ecbb68;
    --gold-deep: #d9a445;
    --gold-bright: #f0c170;
    --ink-light: #ffffff;
    --photo-light: #c9c9c4;
    --photo-tan: #8a5f3e;
  }
  * { box-sizing: border-box; margin: 0; padding: 0; }
  html, body { width: 1200px; height: 780px; overflow: hidden; }
  body {
    background: var(--stage);
    font-family: "Open Sans", Arial, sans-serif;
    display: flex;
    align-items: center;
    justify-content: center;
    gap: 40px;
  }
  .card {
    position: relative;
    width: 540px;
    height: 309px;
    overflow: hidden;
    border-radius: 3px;
  }

  /* Front */
  .card-front { background: var(--navy); color: var(--ink-light); }
  .brand {
    position: absolute;
    display: flex;
    align-items: center;
    gap: 10px;
    color: var(--gold-bright);
    font-weight: 600;
    text-transform: uppercase;
  }
  .brand-front { top: 26px; left: 230px; font-size: 17px; letter-spacing: 1.5px; }
  .brand-mark {
    flex: none;
    border: 2px solid currentColor;
    border-radius: 50%;
  }
  .brand-front .brand-mark { width: 40px; height: 40px; }

  .name-band {
    position: absolute;
    top: 88px;
    left: 0;
    width: 360px;
    height: 62px;
    padding: 6px 0 0 26px;
    background: linear-gradient(90deg, var(--gold) 0%, #b48d5e 45%, rgba(120,110,120,0.55) 80%, rgba(34,48,90,0) 100%);
  }
  .person-name { font-size: 30px; font-weight: 700; line-height: 1.1; }
  .person-title { font-size: 11.5px; font-weight: 400; margin-top: 2px; }

  .address {
    position: absolute;
    top: 160px;
    left: 26px;
    font-size: 14px;
    line-height: 1.35;
  }
  .contacts {
    position: absolute;
    top: 210px;
    left: 10px;
    list-style: none;
    font-size: 14px;
    line-height: 1.6;
  }
  .contacts li { display: flex; align-items: center; gap: 6px; }
  .contacts svg { width: 12px; height: 12px; flex: none; fill: none; stroke: var(--gold); stroke-width: 2; }

  .portrait {
    position: absolute;
    left: 300px;
    top: 118px;
    width: 420px;
    height: 420px;
    border-radius: 50%;
    background: linear-gradient(160deg, var(--photo-light) 0%, #b9b3a8 40%, var(--photo-tan) 75%);
    box-shadow: 0 0 0 6px var(--navy), 0 0 0 9px var(--gold);
  }

  /* Back */
  .card-back {
    background: var(--gold);
    display: flex;
    align-items: center;
    justify-content: center;
  }
  .brand-back {
    position: static;
    color: var(--gold-deep);
    font-size: 34px;
    letter-spacing: 3px;
    gap: 18px;
  }
  .brand-back .brand-mark { width: 86px; height: 86px; border-width: 3px; }
</style>
</head>
<body>

  <section class="card card-front" aria-label="Business card front">
    <div class="portrait" role="img" aria-label="Portrait photo of Odette Marchand in a tan suit"></div>

    <div class="brand brand-front">
      <span class="brand-name">Dovecote Realty</span>
      <span class="brand-mark"></span>
    </div>

    <div class="name-band">
      <p class="person-name">Odette Marchand</p>
      <p class="person-title">Real Estate Advisor and Sales Manager</p>
    </div>

    <p class="address">87 Tarrow Quay,<br>Boston MA 02114</p>

    <ul class="contacts">
      <li>
        <svg viewBox="0 0 24 24"><path d="M5 3h4l2 5-3 2a12 12 0 0 0 6 6l2-3 5 2v4a2 2 0 0 1-2 2A18 18 0 0 1 3 5a2 2 0 0 1 2-2z"/></svg>
        (617) 555-0137
      </li>
      <li>
        <svg viewBox="0 0 24 24"><circle cx="12" cy="12" r="9"/><path d="M3 12h18M12 3c3 3 3 15 0 18M12 3c-3 3-3 15 0 18"/></svg>
        www.dovecoteprops.com
      </li>
      <li>
        <svg viewBox="0 0 24 24"><rect x="3" y="5" width="18" height="14" rx="1"/><path d="M3 6l9 7 9-7"/></svg>
        odette@dovecoteprops.com
      </li>
    </ul>
  </section>

  <section class="card card-back" aria-label="Business card back">
    <div class="brand brand-back">
      <span class="brand-name">Dovecote Realty</span>
      <span class="brand-mark"></span>
    </div>
  </section>

</body>
</html>
```